Travel Agency Website - Simple General

Need a 7 page simple design that is pretty repetitive. Need to be able to load quickly that is SEO optimized. Trying to give ideas on what they can do, be personal as we are local, but at the same time come across as professional and get information easily with little burden.

- Landing Page
- Brimwell Vacations Page
- Family Trips
- Road Trips from Texas
- Other Destinations
- About Us Page
- Contact Us Page

Target Market(s)

Families

Coding

Coded - Design and coding required

Number of Pages Required

5+ page

Colors

Designer to choose colors to be used in the design.

Requirements
Must have
• Like it to flow easily with our logo. Use that for colors, etc.

```html
<!DOCTYPE html>
<html lang="en">
<head>
<meta charset="utf-8">
<title>Hum Along Travel Co. — Website Pages</title>
<link rel="stylesheet" href="https://fonts.googleapis.com/css2?family=Gilda+Display&family=Sacramento&family=Montserrat:wght@400;500;600;700&display=swap">
<style>
:root{
  --sage:#dbe8df;
  --cream:#fdf9f1;
  --card:#fffdf9;
  --teal:#1f5d64;
  --teal-bar:#21595f;
  --btn:#2b8480;
  --gold:#c58b3c;
  --ink:#55605f;
  --line:#e6e1d6;
}
*{box-sizing:border-box}
html,body{margin:0;width:1200px;height:2209px;overflow:hidden;background:var(--sage)}
.stage{position:relative;width:1400px;height:2577px;transform:scale(0.857143);transform-origin:0 0}
.section-label{position:absolute;width:579px;text-align:center;font:600 14.5px/1 'Montserrat',sans-serif;letter-spacing:1.4px;color:#24666b;margin:0}
.page{position:absolute;width:579px;background:var(--cream);overflow:hidden}
.col-left{left:73px}
.col-right{left:722px}

/* navigation */
.nav{position:absolute;top:31px;left:58px;right:58px;display:flex;justify-content:space-between;z-index:3}
.nav ul{display:flex;gap:8px;list-style:none;margin:0;padding:0;font:600 4.6px/1 'Montserrat',sans-serif;color:var(--gold);letter-spacing:.3px}
.nav li.on{text-decoration:underline}
.brand{position:absolute;top:27px;left:50%;transform:translateX(-50%);display:flex;align-items:center;gap:4px;z-index:3;white-space:nowrap}
.brand-dot{width:7px;height:7px;border-radius:50%;background:var(--gold)}
.brand-name{font:400 13px/1 'Gilda Display',serif;color:var(--teal)}

/* hero */
.hero-photo{position:absolute;left:0;right:0;top:40px;height:234px}
.title{position:absolute;left:0;right:0;text-align:center;margin:0;font:400 25px/24px 'Gilda Display',serif;color:var(--teal);letter-spacing:.3px;z-index:2}
.script{font:400 33px/0 'Sacramento',cursive;letter-spacing:0;text-transform:none}
.plane{vertical-align:middle;margin-left:-2px}

/* footer */
.foot{position:absolute;left:0;right:0;bottom:0;height:13px;background:var(--teal-bar);display:flex;align-items:center;justify-content:space-between;padding:0 58px;font:500 4.4px/1 'Montserrat',sans-serif;color:#fff}
.foot span{display:flex;align-items:center;gap:3px}
.foot .social i{display:block;width:5px;height:5px;background:#fff;border-radius:1px}

/* photo placeholders */
.shot{position:absolute}
.caption{position:absolute;width:109px;text-align:center;font:400 10px/10px 'Gilda Display',serif;color:var(--teal);margin:0}

/* gallery */
.gallery-head{position:absolute;left:58px;top:297px;margin:0;font:400 10px/1 'Gilda Display',serif;color:var(--teal);letter-spacing:.2px}
.arrows{position:absolute;right:58px;top:292px;display:flex;gap:5px}
.arrows span{width:15px;height:15px;background:var(--btn);display:flex;align-items:center;justify-content:center}
.fade{opacity:.55}

/* forms */
.form-head{position:absolute;left:315px;margin:0;font:400 10px/1 'Gilda Display',serif;color:var(--teal)}
.card{position:absolute;background:var(--card);border:1px solid #eee9df;box-shadow:0 1px 4px rgba(60,60,40,.06);padding:7px 9px 9px}
.lbl{display:block;font:500 4.3px/1 'Montserrat',sans-serif;color:var(--ink);margin:6px 0 3px}
.field{position:relative;height:12px;border:1px solid var(--line);background:#fff;display:flex;align-items:center;gap:3px;padding:0 5px;font:400 4.3px/1 'Montserrat',sans-serif;color:#6a706e}
.field.select::after{content:"";position:absolute;right:5px;top:5px;border:2px solid transparent;border-top:2.4px solid #555;border-bottom:0}
.field.area{height:20px;align-items:flex-start;padding-top:4px}
.field i{display:block;width:4px;height:4px;background:#8d9491;border-radius:1px}
.row{display:flex;gap:6px}
.row>div{flex:1}
.btn{display:flex;align-items:center;justify-content:center;height:12px;margin-top:8px;background:var(--btn);color:#fff;font:600 4.3px/1 'Montserrat',sans-serif;letter-spacing:.3px}
.radio-row{display:flex;gap:12px;font:700 4.3px/1 'Montserrat',sans-serif;color:var(--teal);padding:4px 0 2px}
.radio-row span{display:flex;align-items:center;gap:3px}
.radio-row b{display:block;width:5px;height:5px;border:1px solid var(--teal);border-radius:50%}
.radio-row b.on{background:var(--teal)}

/* table */
.packages{position:absolute;left:58px;top:333px;width:463px;border-collapse:collapse;font:400 4.3px/1.35 'Montserrat',sans-serif;color:var(--ink);text-align:center}
.packages th{background:#f1f0ea;font-weight:700;color:var(--teal);height:10px;font-size:4px;letter-spacing:.2px}
.packages td{border-bottom:1px solid var(--line);height:48px;vertical-align:middle;padding:0 3px}
.dest{display:flex;align-items:center;gap:5px;text-align:left}
.dest .thumb{width:42px;height:35px;flex:none}
.dest strong{display:block;font:400 9.5px/9px 'Gilda Display',serif;color:var(--teal)}
.dest small{font-size:3.8px}

/* about */
.about-title{position:absolute;left:333px;top:525px;margin:0;font:400 26px/24px 'Gilda Display',serif;color:var(--teal)}
.about-copy{position:absolute;left:333px;width:190px;margin:0;font:400 4.6px/1.55 'Montserrat',sans-serif;color:var(--ink)}
.tagline{position:absolute;left:333px;top:669px;margin:0;font:400 10.5px/1 'Gilda Display',serif;color:var(--teal)}
.book{position:absolute;left:333px;top:690px;width:90px;height:15px;background:var(--btn);color:#fff;display:flex;align-items:center;justify-content:center;font:600 4.5px/1 'Montserrat',sans-serif}
</style>
</head>
<body>
<div class="stage">

<!-- ============ LANDING ============ -->
<h2 class="section-label" style="left:73px;top:29px">LANDING PAGE</h2>
<section class="page col-left" style="top:56px;height:325px">
  <nav class="nav"><ul><li class="on">HOME</li><li>ABOUT US</li><li>BRIMWELL VACATIONS</li><li>FAMILY TRIPS</li></ul><ul><li>TEXAS ROAD TRIPS</li><li>OTHER DESTINATIONS</li><li>CONTACT US</li></ul></nav>
  <div class="brand"><span class="brand-dot"></span><span class="brand-name">Hum Along</span></div>
  <h1 class="title" style="top:73px">LET'S PLAN A TRIP YOU'LL<br>NEVER <span class="script">Forget</span><svg class="plane" viewBox="0 0 48 16" width="40" height="13"><path d="M2 12C14 15 22 4 30 8S37 11 39 7" fill="none" stroke="#c58b3c" stroke-width=".8" stroke-dasharray="2 1.5"/><path d="M39 7l8-4-2.5 3 1.5 3.5-1.5.2-2-2.5-3 1.3z" fill="#1f5d64"/></svg></h1>
  <div class="shot" role="img" aria-label="Theme park entrance gate over a sunny road" style="left:58px;top:129px;width:109px;height:138px;background:linear-gradient(180deg,#4d8fd6 0%,#7fb5e6 40%,#9a9ea3 60%,#6b6f73 100%)"></div>
  <div class="shot" role="img" aria-label="Family walking on a beach at sunset" style="left:176px;top:129px;width:109px;height:138px;background:linear-gradient(180deg,#d7a35f 0%,#efc48a 35%,#e7c7a3 65%,#c99e74 100%)"></div>
  <div class="shot" role="img" aria-label="Motorhome parked by the beach" style="left:293px;top:129px;width:109px;height:138px;background:linear-gradient(180deg,#8fb9dd 0%,#c9d6de 40%,#8b8f94 70%,#d9ccb4 100%)"></div>
  <div class="shot" role="img" aria-label="Kids sledding in the snow" style="left:410px;top:129px;width:109px;height:138px;background:linear-gradient(180deg,#f2f4f7 0%,#c9d7e6 45%,#5d7794 75%,#e9eef3 100%)"></div>
  <p class="caption" style="left:58px;top:271px">BRIMWELL VACATIONS<br>– LAND AND SEA</p>
  <p class="caption" style="left:176px;top:271px">FAMILY TRIPS</p>
  <p class="caption" style="left:293px;top:271px">TEXAS ROAD<br>TRIPS</p>
  <p class="caption" style="left:410px;top:271px">OTHER<br>DESTINATIONS</p>
  <footer class="foot"><span><svg width="5" height="5" viewBox="0 0 10 10"><path d="M2 1l2 2-1 1.5c.8 1.5 1.8 2.5 3.3 3.3L7.8 6.8l2 2L8.5 10C4 9.5.5 6 0 1.5z" fill="#fff"/></svg>Call Us For More Information: 111.111.1111</span><span class="social"><i></i><i></i></span><span><svg width="5" height="4" viewBox="0 0 10 8"><rect width="10" height="8" fill="#fff"/><path d="M0 0l5 4 5-4" stroke="#21595f" fill="none"/></svg>Email: hello@humalongtravel.com</span></footer>
</section>

<!-- ============ BRIMWELL VACATIONS ============ -->
<h2 class="section-label" style="left:73px;top:409px">BRIMWELL VACATIONS PAGE</h2>
<section class="page col-left" style="top:436px;height:597px">
  <div class="hero-photo" role="img" aria-label="Fairytale castle above treetops at golden hour" style="background:linear-gradient(180deg,var(--cream) 0%,rgba(253,249,241,0) 40%),linear-gradient(180deg,#eef0ef 0%,#dce3e7 45%,#c8b597 75%,#7d7a4c 100%)"></div>
  <nav class="nav"><ul><li>HOME</li><li>ABOUT US</li><li class="on">BRIMWELL VACATIONS</li><li>FAMILY TRIPS</li></ul><ul><li>TEXAS ROAD TRIPS</li><li>OTHER DESTINATIONS</li><li>CONTACT US</li></ul></nav>
  <div class="brand"><span class="brand-dot"></span><span class="brand-name">Hum Along</span></div>
  <h1 class="title" style="top:83px">MAGICAL BRIMWELL <span class="script">Vacations</span><svg class="plane" viewBox="0 0 48 16" width="40" height="13"><path d="M2 12C14 15 22 4 30 8S37 11 39 7" fill="none" stroke="#c58b3c" stroke-width=".8" stroke-dasharray="2 1.5"/><path d="M39 7l8-4-2.5 3 1.5 3.5-1.5.2-2-2.5-3 1.3z" fill="#1f5d64"/></svg></h1>
  <div class="shot" role="img" aria-label="Theme park welcome arch with palm trees and blue sky" style="left:58px;top:299px;width:236px;height:259px;background:linear-gradient(180deg,#1f6fd1 0%,#4b92df 35%,#3f5b3c 62%,#6d7378 80%,#4f5357 100%)"></div>
  <form class="card" style="left:315px;top:300px;width:206px">
    <div class="radio-row"><span><b class="on"></b>BRIMWELL WORLD / BRIMWELL LAND</span><span><b></b>BRIMWELL CRUISE</span></div>
    <label class="lbl">How Many People?</label><div class="field select"><i></i>1 - 5</div>
    <div class="row"><div><label class="lbl">Start Date</label><div class="field select"><i></i>26 June, 2026</div></div><div><label class="lbl">End Date</label><div class="field select"><i></i>28 June, 2026</div></div></div>
    <label class="lbl">How Many Days at the Parks?</label><div class="field select"><i></i>2 - 3 Days</div>
    <label class="lbl">What Kind of Trip Are You Looking For?</label><div class="field select"><i></i>Budget Friendly</div>
    <label class="lbl">Any Preferred Resorts?</label><div class="field select"><i></i>Preferred Resort 1</div>
    <label class="lbl">Any Additional Notes:</label><div class="field area"><i></i>Type Your Message...</div>
    <div class="btn">SUBMIT AND CONTINUE</div>
  </form>
  <footer class="foot"><span><svg width="5" height="5" viewBox="0 0 10 10"><path d="M2 1l2 2-1 1.5c.8 1.5 1.8 2.5 3.3 3.3L7.8 6.8l2 2L8.5 10C4 9.5.5 6 0 1.5z" fill="#fff"/></svg>Call Us For More Information: 111.111.1111</span><span class="social"><i></i><i></i></span><span><svg width="5" height="4" viewBox="0 0 10 8"><rect width="10" height="8" fill="#fff"/><path d="M0 0l5 4 5-4" stroke="#21595f" fill="none"/></svg>Email: hello@humalongtravel.com</span></footer>
</section>

<!-- ============ FAMILY TRIPS ============ -->
<h2 class="section-label" style="left:73px;top:1062px">FAMILY TRIPS PAGE</h2>
<section class="page col-left" style="top:1089px;height:776px">
  <div class="hero-photo" role="img" aria-label="Parents and child walking along the shore at sunset" style="background:linear-gradient(180deg,var(--cream) 0%,rgba(253,249,241,0) 38%),linear-gradient(180deg,#f4eadc 0%,#ecc996 40%,#c9a27c 65%,#9d8a78 85%,#b3a595 100%)"></div>
  <nav class="nav"><ul><li>HOME</li><li>ABOUT US</li><li>BRIMWELL VACATIONS</li><li class="on">FAMILY TRIPS</li></ul><ul><li>TEXAS ROAD TRIPS</li><li>OTHER DESTINATIONS</li><li>CONTACT US</li></ul></nav>
  <div class="brand"><span class="brand-dot"></span><span class="brand-name">Hum Along</span></div>
  <h1 class="title" style="top:73px">CREATE UNFORGETTABLE<br>FAMILY <span class="script">Memories</span><svg class="plane" viewBox="0 0 48 16" width="40" height="13"><path d="M2 12C14 15 22 4 30 8S37 11 39 7" fill="none" stroke="#c58b3c" stroke-width=".8" stroke-dasharray="2 1.5"/><path d="M39 7l8-4-2.5 3 1.5 3.5-1.5.2-2-2.5-3 1.3z" fill="#1f5d64"/></svg></h1>
  <h3 class="gallery-head">PICTURES OF TRIPS OUR FAMILY TOOK</h3>
  <div class="arrows"><span><svg width="7" height="5" viewBox="0 0 14 10"><path d="M13 5H2M6 1L2 5l4 4" stroke="#fff" stroke-width="1.6" fill="none"/></svg></span><span><svg width="7" height="5" viewBox="0 0 14 10"><path d="M1 5h11M8 1l4 4-4 4" stroke="#fff" stroke-width="1.6" fill="none"/></svg></span></div>
  <div class="shot" role="img" aria-label="Mother and child in a bright pool" style="left:58px;top:318px;width:109px;height:138px;background:linear-gradient(180deg,#2a7cc8,#56a7e4 60%,#8fd0f2)"></div>
  <div class="shot" role="img" aria-label="Couple sitting on a wooden boat under palms" style="left:176px;top:327px;width:109px;height:138px;background:linear-gradient(180deg,#6f8a4a,#a88a66 50%,#8a6d52)"></div>
  <div class="shot" role="img" aria-label="Family packing the back of a car" style="left:294px;top:318px;width:109px;height:138px;background:linear-gradient(180deg,#3d4248,#7b6a5a 55%,#c8b9a6)"></div>
  <div class="shot" role="img" aria-label="Family looking over a lake from a hill" style="left:411px;top:327px;width:109px;height:138px;background:linear-gradient(180deg,#d8c7a8,#7d93ad 45%,#6d7a55 85%)"></div>
  <div class="shot fade" role="img" aria-label="Traveler by a lake" style="left:530px;top:336px;width:60px;height:138px;background:linear-gradient(180deg,#9aa7a8,#c8c3b6)"></div>
  <div class="shot" role="img" aria-label="Family hiking on rocky mountain peaks" style="left:58px;top:514px;width:236px;height:224px;background:linear-gradient(180deg,#a9c3db 0%,#87a3bb 40%,#6d7f66 70%,#b8b2a4 100%)"></div>
  <h3 class="form-head" style="top:514px">PLEASE FILLOUT THE FORM BELOW</h3>
  <form class="card" style="left:315px;top:532px;width:206px">
    <label class="lbl">How Many People in Your Party?</label><div class="field select"><i></i>1 - 5</div>
    <label class="lbl">When Would You Like To Go? ( Dates Start — Finish )</label>
    <div class="row"><div><div class="field select"><i></i>26 June, 2026</div></div><div><div class="field select"><i></i>28 June, 2026</div></div></div>
    <label class="lbl">Which Trip Are You Interested In?</label><div class="field select"><i></i>Beach</div>
    <label class="lbl">What Kind of Trip Are You Looking For?</label><div class="field select"><i></i>Budget Friendly</div>
    <label class="lbl">Any Additional Notes:</label><div class="field area"><i></i>Type Your Message...</div>
    <div class="btn">SUBMIT AND CONTINUE</div>
  </form>
  <footer class="foot"><span><svg width="5" height="5" viewBox="0 0 10 10"><path d="M2 1l2 2-1 1.5c.8 1.5 1.8 2.5 3.3 3.3L7.8 6.8l2 2L8.5 10C4 9.5.5 6 0 1.5z" fill="#fff"/></svg>Call Us For More Information: 111.111.1111</span><span class="social"><i></i><i></i></span><span><svg width="5" height="4" viewBox="0 0 10 8"><rect width="10" height="8" fill="#fff"/><path d="M0 0l5 4 5-4" stroke="#21595f" fill="none"/></svg>Email: hello@humalongtravel.com</span></footer>
</section>

<!-- ============ CONTACT ============ -->
<h2 class="section-label" style="left:78px;top:1891px">CONTACT US PAGE</h2>
<section class="page col-left" style="top:1917px;height:529px">
  <div class="hero-photo" role="img" aria-label="Family playing on a beach with rocks" style="background:linear-gradient(180deg,var(--cream) 0%,rgba(253,249,241,0) 38%),linear-gradient(180deg,#f1f0ec 0%,#dfe3e2 40%,#b9bcb7 60%,#d9cfbf 80%,#e8dfcf 100%)"></div>
  <nav class="nav"><ul><li>HOME</li><li>ABOUT US</li><li>BRIMWELL VACATIONS</li><li>FAMILY TRIPS</li></ul><ul><li>TEXAS ROAD TRIPS</li><li>OTHER DESTINATIONS</li><li class="on">CONTACT US</li></ul></nav>
  <div class="brand"><span class="brand-dot"></span><span class="brand-name">Hum Along</span></div>
  <h1 class="title" style="top:83px">GET IN TOUCH <span class="script">With Us</span><svg class="plane" viewBox="0 0 48 16" width="40" height="13"><path d="M2 12C14 15 22 4 30 8S37 11 39 7" fill="none" stroke="#c58b3c" stroke-width=".8" stroke-dasharray="2 1.5"/><path d="M39 7l8-4-2.5 3 1.5 3.5-1.5.2-2-2.5-3 1.3z" fill="#1f5d64"/></svg></h1>
  <div class="shot" role="img" aria-label="Smiling family in sun hats by the sea" style="left:58px;top:300px;width:236px;height:191px;background:linear-gradient(180deg,#7fc3e4 0%,#a8d6ea 40%,#2e8c7e 70%,#d8b394 100%)"></div>
  <h3 class="form-head" style="top:302px">PLEASE FILLOUT THE FORM BELOW</h3>
  <form class="card" style="left:315px;top:318px;width:206px">
    <label class="lbl">Name</label><div class="field"><i></i>Enter Your Full Name</div>
    <label class="lbl">Enter Your Email</label><div class="field"><i></i>youremail@mail.com</div>
    <label class="lbl">Phone</label><div class="field"><i></i>Enter Your Contact Number</div>
    <label class="lbl">Any Additional Notes:</label><div class="field area"><i></i>Type Your Message...</div>
    <div class="btn">SUBMIT AND CONTINUE</div>
  </form>
  <footer class="foot"><span><svg width="5" height="5" viewBox="0 0 10 10"><path d="M2 1l2 2-1 1.5c.8 1.5 1.8 2.5 3.3 3.3L7.8 6.8l2 2L8.5 10C4 9.5.5 6 0 1.5z" fill="#fff"/></svg>Call Us For More Information: 111.111.1111</span><span class="social"><i></i><i></i></span><span><svg width="5" height="4" viewBox="0 0 10 8"><rect width="10" height="8" fill="#fff"/><path d="M0 0l5 4 5-4" stroke="#21595f" fill="none"/></svg>Email: hello@humalongtravel.com</span></footer>
</section>

<!-- ============ OTHER DESTINATIONS ============ -->
<h2 class="section-label" style="left:722px;top:29px">OTHER DESTINATIONS PAGE</h2>
<section class="page col-right" style="top:56px;height:775px">
  <div class="hero-photo" role="img" aria-label="Family sitting in the open back of an SUV on the beach" style="background:linear-gradient(180deg,var(--cream) 0%,rgba(253,249,241,0) 38%),linear-gradient(180deg,#f0eeea 0%,#e2dfda 40%,#bdb7ad 65%,#d8cbb4 85%,#e9dcc4 100%)"></div>
  <nav class="nav"><ul><li>HOME</li><li>ABOUT US</li><li>BRIMWELL VACATIONS</li><li>FAMILY TRIPS</li></ul><ul><li>TEXAS ROAD TRIPS</li><li class="on">OTHER DESTINATIONS</li><li>CONTACT US</li></ul></nav>
  <div class="brand"><span class="brand-dot"></span><span class="brand-name">Hum Along</span></div>
  <h1 class="title" style="top:81px">DISCOVER SOMEWHERE <span class="script">New</span><svg class="plane" viewBox="0 0 48 16" width="40" height="13"><path d="M2 12C14 15 22 4 30 8S37 11 39 7" fill="none" stroke="#c58b3c" stroke-width=".8" stroke-dasharray="2 1.5"/><path d="M39 7l8-4-2.5 3 1.5 3.5-1.5.2-2-2.5-3 1.3z" fill="#1f5d64"/></svg></h1>
  <h3 class="gallery-head">PICTURES OF TRIPS OUR FAMILY TOOK</h3>
  <div class="arrows"><span><svg width="7" height="5" viewBox="0 0 14 10"><path d="M13 5H2M6 1L2 5l4 4" stroke="#fff" stroke-width="1.6" fill="none"/></svg></span><span><svg width="7" height="5" viewBox="0 0 14 10"><path d="M1 5h11M8 1l4 4-4 4" stroke="#fff" stroke-width="1.6" fill="none"/></svg></span></div>
  <div class="shot" role="img" aria-label="Mother and child in a bright pool" style="left:58px;top:318px;width:109px;height:138px;background:linear-gradient(180deg,#2a7cc8,#56a7e4 60%,#8fd0f2)"></div>
  <div class="shot" role="img" aria-label="Couple sitting on a wooden boat under palms" style="left:176px;top:327px;width:109px;height:138px;background:linear-gradient(180deg,#6f8a4a,#a88a66 50%,#8a6d52)"></div>
  <div class="shot" role="img" aria-label="Family packing the back of a car" style="left:294px;top:318px;width:109px;height:138px;background:linear-gradient(180deg,#3d4248,#7b6a5a 55%,#c8b9a6)"></div>
  <div class="shot" role="img" aria-label="Family looking over a lake from a hill" style="left:411px;top:327px;width:109px;height:138px;background:linear-gradient(180deg,#d8c7a8,#7d93ad 45%,#6d7a55 85%)"></div>
  <div class="shot fade" role="img" aria-label="Traveler by a lake" style="left:530px;top:336px;width:60px;height:138px;background:linear-gradient(180deg,#9aa7a8,#c8c3b6)"></div>
  <div class="shot" role="img" aria-label="Family cheering in the snow with skis" style="left:58px;top:513px;width:236px;height:224px;background:linear-gradient(180deg,#3f7fc9 0%,#8fb7e0 40%,#c94f8e 60%,#eef2f6 85%,#ffffff 100%)"></div>
  <h3 class="form-head" style="top:513px">PLEASE FILLOUT THE FORM BELOW</h3>
  <form class="card" style="left:315px;top:531px;width:206px">
    <label class="lbl">How Many People in Your Party?</label><div class="field select"><i></i>1 - 5</div>
    <label class="lbl">When Would You Like To Go? ( Dates Start — Finish )</label>
    <div class="row"><div><div class="field select"><i></i>26 June, 2026</div></div><div><div class="field select"><i></i>28 June, 2026</div></div></div>
    <label class="lbl">Which Trip Are You Interested In?</label><div class="field select"><i></i>Beach</div>
    <label class="lbl">What Kind of Trip Are You Looking For?</label><div class="field select"><i></i>Budget Friendly</div>
    <label class="lbl">Any Additional Notes:</label><div class="field area"><i></i>Type Your Message...</div>
    <div class="btn">SUBMIT AND CONTINUE</div>
  </form>
  <footer class="foot"><span><svg width="5" height="5" viewBox="0 0 10 10"><path d="M2 1l2 2-1 1.5c.8 1.5 1.8 2.5 3.3 3.3L7.8 6.8l2 2L8.5 10C4 9.5.5 6 0 1.5z" fill="#fff"/></svg>Call Us For More Information: 111.111.1111</span><span class="social"><i></i><i></i></span><span><svg width="5" height="4" viewBox="0 0 10 8"><rect width="10" height="8" fill="#fff"/><path d="M0 0l5 4 5-4" stroke="#21595f" fill="none"/></svg>Email: hello@humalongtravel.com</span></footer>
</section>

<!-- ============ ABOUT ============ -->
<h2 class="section-label" style="left:722px;top:859px">ABOUT US PAGE</h2>
<section class="page col-right" style="top:886px;height:763px">
  <div class="hero-photo" role="img" aria-label="Family playing in turquoise surf" style="background:linear-gradient(180deg,var(--cream) 0%,rgba(253,249,241,0) 38%),linear-gradient(180deg,#eef6f6 0%,#bfe3ea 35%,#3ab6c7 55%,#7fd0d8 72%,#e4ddd0 100%)"></div>
  <nav class="nav"><ul><li>HOME</li><li class="on">ABOUT US</li><li>BRIMWELL VACATIONS</li><li>FAMILY TRIPS</li></ul><ul><li>TEXAS ROAD TRIPS</li><li>OTHER DESTINATIONS</li><li>CONTACT US</li></ul></nav>
  <div class="brand"><span class="brand-dot"></span><span class="brand-name">Hum Along</span></div>
  <h1 class="title" style="top:69px">VACATION PLANNING<br>MADE <span class="script">Simple</span><svg class="plane" viewBox="0 0 48 16" width="40" height="13"><path d="M2 12C14 15 22 4 30 8S37 11 39 7" fill="none" stroke="#c58b3c" stroke-width=".8" stroke-dasharray="2 1.5"/><path d="M39 7l8-4-2.5 3 1.5 3.5-1.5.2-2-2.5-3 1.3z" fill="#1f5d64"/></svg></h1>
  <h3 class="gallery-head">LET'S CHECKOUT OUR LATEST GALLERY</h3>
  <div class="arrows"><span><svg width="7" height="5" viewBox="0 0 14 10"><path d="M13 5H2M6 1L2 5l4 4" stroke="#fff" stroke-width="1.6" fill="none"/></svg></span><span><svg width="7" height="5" viewBox="0 0 14 10"><path d="M1 5h11M8 1l4 4-4 4" stroke="#fff" stroke-width="1.6" fill="none"/></svg></span></div>
  <div class="shot" role="img" aria-label="Mother and child in a bright pool" style="left:58px;top:318px;width:109px;height:138px;background:linear-gradient(180deg,#2a7cc8,#56a7e4 60%,#8fd0f2)"></div>
  <div class="shot" role="img" aria-label="Couple sitting on a wooden boat under palms" style="left:176px;top:327px;width:109px;height:138px;background:linear-gradient(180deg,#6f8a4a,#a88a66 50%,#8a6d52)"></div>
  <div class="shot" role="img" aria-label="Family packing the back of a car" style="left:294px;top:318px;width:109px;height:138px;background:linear-gradient(180deg,#3d4248,#7b6a5a 55%,#c8b9a6)"></div>
  <div class="shot" role="img" aria-label="Family looking over a lake from a hill" style="left:411px;top:327px;width:109px;height:138px;background:linear-gradient(180deg,#d8c7a8,#7d93ad 45%,#6d7a55 85%)"></div>
  <div class="shot fade" role="img" aria-label="Traveler by a lake" style="left:530px;top:336px;width:60px;height:138px;background:linear-gradient(180deg,#9aa7a8,#c8c3b6)"></div>
  <div class="shot" role="img" aria-label="Family with luggage walking through a bright airport" style="left:58px;top:514px;width:236px;height:210px;background:linear-gradient(180deg,#e9ecec 0%,#d9dcd8 40%,#bfae96 70%,#c9c3b9 100%)"></div>
  <h2 class="about-title">DESTINATIONS<br><span class="script">Designed</span> AROUND<br>YOU.<svg class="plane" viewBox="0 0 48 16" width="40" height="13"><path d="M2 12C14 15 22 4 30 8S37 11 39 7" fill="none" stroke="#c58b3c" stroke-width=".8" stroke-dasharray="2 1.5"/><path d="M39 7l8-4-2.5 3 1.5 3.5-1.5.2-2-2.5-3 1.3z" fill="#1f5d64"/></svg></h2>
  <p class="about-copy" style="top:605px">We are a small local team who plan trips the way we plan our own, with care for every detail. From park days to quiet beaches, we match each family with the places, pace and budget that suit them best.</p>
  <p class="about-copy" style="top:642px">Tell us what you love and we handle the rest, from booking to the last day home.</p>
  <p class="tagline">CARE, EXPERTISE, AND DEDICATION.</p>
  <div class="book">BOOK A TRIP</div>
  <footer class="foot"><span><svg width="5" height="5" viewBox="0 0 10 10"><path d="M2 1l2 2-1 1.5c.8 1.5 1.8 2.5 3.3 3.3L7.8 6.8l2 2L8.5 10C4 9.5.5 6 0 1.5z" fill="#fff"/></svg>Call Us For More Information: 111.111.1111</span><span class="social"><i></i><i></i></span><span><svg width="5" height="4" viewBox="0 0 10 8"><rect width="10" height="8" fill="#fff"/><path d="M0 0l5 4 5-4" stroke="#21595f" fill="none"/></svg>Email: hello@humalongtravel.com</span></footer>
</section>

<!-- ============ TEXAS ROAD TRIPS ============ -->
<h2 class="section-label" style="left:718px;top:1685px">ROAD TRIPS FROM TEXAS PAGE</h2>
<section class="page col-right" style="top:1714px;height:776px">
  <div class="hero-photo" role="img" aria-label="Winding coastal road beside the sea" style="background:linear-gradient(180deg,var(--cream) 0%,rgba(253,249,241,0) 38%),linear-gradient(180deg,#eef0ee 0%,#cfd9de 35%,#6f8e9c 55%,#5a6a6e 75%,#587049 100%)"></div>
  <nav class="nav"><ul><li>HOME</li><li>ABOUT US</li><li>BRIMWELL VACATIONS</li><li>FAMILY TRIPS</li></ul><ul><li class="on">TEXAS ROAD TRIPS</li><li>OTHER DESTINATIONS</li><li>CONTACT US</li></ul></nav>
  <div class="brand"><span class="brand-dot"></span><span class="brand-name">Hum Along</span></div>
  <h1 class="title" style="top:83px">ROAD TRIPS FROM <span class="script">Texas</span><svg class="plane" viewBox="0 0 48 16" width="40" height="13"><path d="M2 12C14 15 22 4 30 8S37 11 39 7" fill="none" stroke="#c58b3c" stroke-width=".8" stroke-dasharray="2 1.5"/><path d="M39 7l8-4-2.5 3 1.5 3.5-1.5.2-2-2.5-3 1.3z" fill="#1f5d64"/></svg></h1>
  <h3 class="gallery-head" style="top:302px">BEST TEXAS TRAVEL PACKAGES AT A GLANCE FOR JUNE</h3>
  <div class="arrows" style="top:298px"><span><svg width="7" height="5" viewBox="0 0 14 10"><path d="M13 5H2M6 1L2 5l4 4" stroke="#fff" stroke-width="1.6" fill="none"/></svg></span><span><svg width="7" height="5" viewBox="0 0 14 10"><path d="M1 5h11M8 1l4 4-4 4" stroke="#fff" stroke-width="1.6" fill="none"/></svg></span></div>
  <table class="packages">
    <thead><tr><th style="width:115px">DESTINATION</th><th style="width:62px">DURATION</th><th style="width:74px">DESTINATION HIGHLIGHTS</th><th style="width:88px">DISTANCE FROM TYLER, TEXAS</th><th style="width:62px">BUDGET</th><th>SUITABLE FOR</th></tr></thead>
    <tbody>
      <tr><td><div class="dest"><span class="thumb" role="img" aria-label="Pine forest lake" style="background:linear-gradient(180deg,#8aa5b8,#4f6b3f)"></span><div><strong>PINEY<br>WOODS<br>ESCAPE</strong><small>East Texas</small></div></div></td><td>4 Days / 3 Nights</td><td>State Parks, Lakes, Wildlife, Fishing</td><td>200 Miles</td><td>$250 -$500</td><td>Families,<br>Nature Lovers,<br>Adventure Seekers,<br>Couples</td></tr>
      <tr><td><div class="dest"><span class="thumb" role="img" aria-label="Camper van by the coast" style="background:linear-gradient(180deg,#a9c7dc,#e8e6e0 55%,#c9b08a)"></span><div><strong>COASTAL<br>GETAWAY</strong><small>Galveston Port Aransas</small></div></div></td><td>3 Days / 2 Nights</td><td>Beaches, Padre Island, Local Seafood, Aquarium, Sunrise, Beach Walks</td><td>180 Miles</td><td>$350 -$600</td><td>Families,<br>Nature Lovers,<br>Beach Lovers</td></tr>
      <tr><td><div class="dest"><span class="thumb" role="img" aria-label="Rolling hill country vineyards" style="background:linear-gradient(180deg,#c9b27a,#6d7a3a 60%,#4d5a2c)"></span><div><strong>HILL<br>COUNTRY<br>TOUR</strong><small>Fredericksburg, Kerrville</small></div></div></td><td>3 Days / 2 Nights</td><td>Wineries,<br>Small Towns,<br>Natural Springs,<br>Scenic Drives</td><td>150 Miles</td><td>$400 -$600</td><td>Couples, Relaxed<br>Travelers</td></tr>
    </tbody>
  </table>
  <div class="shot" role="img" aria-label="Friends relaxing beside a camper van in green hills" style="left:58px;top:515px;width:236px;height:223px;background:linear-gradient(180deg,#e8d6a8 0%,#b9c08a 40%,#7b8f57 70%,#9aa37a 100%)"></div>
  <h3 class="form-head" style="top:515px">PLEASE FILLOUT THE FORM BELOW</h3>
  <form class="card" style="left:315px;top:533px;width:206px">
    <label class="lbl">How Many People in Your Party?</label><div class="field select"><i></i>1 - 5</div>
    <label class="lbl">When Would You Like To Go? ( Dates Start — Finish )</label>
    <div class="row"><div><div class="field select"><i></i>26 June, 2026</div></div><div><div class="field select"><i></i>28 June, 2026</div></div></div>
    <label class="lbl">Which Trip Are You Interested In?</label><div class="field select"><i></i>Beach</div>
    <label class="lbl">Do You Need a Van Rental (Pinecrest Van Rentals — Tyler, TX)?</label><div class="field select">Yes</div>
    <label class="lbl">Any Additional Notes:</label><div class="field area"><i></i>Type Your Message...</div>
    <div class="btn">SUBMIT AND CONTINUE</div>
  </form>
  <footer class="foot"><span><svg width="5" height="5" viewBox="0 0 10 10"><path d="M2 1l2 2-1 1.5c.8 1.5 1.8 2.5 3.3 3.3L7.8 6.8l2 2L8.5 10C4 9.5.5 6 0 1.5z" fill="#fff"/></svg>Call Us For More Information: 111.111.1111</span><span class="social"><i></i><i></i></span><span><svg width="5" height="4" viewBox="0 0 10 8"><rect width="10" height="8" fill="#fff"/><path d="M0 0l5 4 5-4" stroke="#21595f" fill="none"/></svg>Email: hello@humalongtravel.com</span></footer>
</section>

</div>
</body>
</html>
```